Creative UI design for web application

I need a new UI design for my web application. It will be used by small and micro business owners to plan & implement growth tactics.

I've attached the current design (which I'm open to be changed) - but in particular I need to design the centre of the screen, where the work actually happens.

There needs to be place for a title (YOUR BUSINESS) and description (say 1-2 paragraphs of text) - and am happy to include icons or imagery where makes sense. It may make sense for the user to be able to upload their business logo and name, for example.

This screen will be used by the business owner to understand the real value they offer potential customers and their point of difference - why they exist and why potential customers should care.

They'll use the information they put into this screen to plan things like their messaging.

Following that, there needs to be 2 sections in the dashboard.

The first section is titled "WHO YOU ARE"

The first section will include a number of boxes that the user can input information into, as follows:

- Logo
- Business name
- Business tag line
- Business vision
- Business bio
- Brand colours (these should end up as swatches based on the colour code they enter) - the colour code for each colour swatch should also be visible.
- Key competitors
- SWOT analysis (boxes to enter their strengths, weaknesses, opportunities and threats).

The second section is titled "WHY YOU EXIST"

The second section will include a number of boxes that the user can input information (text) into, as follows:

- Who are your ideal customers?
- What problem are you trying to solve for them?
- What pain points will this remove for them?
- How do you solve it?
- How else could this problem be solved?
- Who offers these other solutions?
- Why is your solution better?
- How much does your solution cost?
- What value are you providing to justify this cost?
- How will this make their life/job easier/better?

They should be able to write a decent amount of information in the boxes.

There should ideally be a place for a description for each of these text fields (for both section 1 & 2) as well so I can give them a little bit more direction around what to put in the box. Alternatively there could be a little icon (say a question mark or "i") that they could click on to view instructions. The instructions will be around 2-4 sentences long for each text field.

You have 2 options:

a) This all needs to appear on the one screen, and the navigation needs to be visible (as per the example attached but feel free to recreate this navigation)

Note: the page can scroll below the fold - but please provide the design for the full length of the page.

b) Potentially the 2 sections could actually be in 2 different items in the menu - YOUR BUSINESS and YOUR VALUE (which would sit next to YOUR BUSINESS and before YOUR CUSTOMER in the screenshot provided). feel free to design them as 2 separate screens if you prefer.

I have attached a screenshot of the app as it stands today (screen shot 2017) which would still exist in the new design but under a different section (the learn section from the plan2 mockup attached)

I have mocked up how this new screen could look if broken into 2 and that's also attached. If you can make this come to life - and look more engaging that would be helpful! :)

Target Market(s)

Small and micro business owners

Industry/Entity Type

Marketing

Number of Pages Required

1 page

Font styles to use
Sans Serif
Other font styles liked:
• Montserrat

Colors
87cfc6
d2a4cc
ffffff
85cae6
e8e8e8
5c5c5c

Requirements
Must have
• Use of my brand colours: #cc8eb2, #76d6c8, #68c7ff as well as white and #595959. Must be visually pleasing / engaging, designed for desktop (as it's a desktop application), really easy to use / navigate.
• Use font Montserrat light & Montserrat Regular or Bold. Mostly should be Montserrat light.
Nice to have
• Would be nice to see how this would look on mobile (as the application is responsive) but this is not mandatory.
Should not have
• Should not look too corporate or dry.

```html
<!DOCTYPE html>
<html lang="en">
<head>
<meta charset="utf-8">
<title>Rootwise – Your Business</title>
<link rel="stylesheet" href="https://fonts.googleapis.com/css2?family=Montserrat:wght@300;400;500;600&display=swap">
<style>
:root{
  --topbar:#3a3a3a;
  --subnav:#85cae6;
  --teal:#87cfc6;
  --pink:#d2a4cc;
  --ink:#333333;
  --text:#5c5c5c;
  --light:#f2f2f2;
  --footer:#5a5a5a;
  --white:#ffffff;
  --line:#dcdcdc;
}
*{box-sizing:border-box;margin:0;padding:0}
html,body{width:1200px;height:2539px;overflow:hidden}
body{position:relative;font-family:'Montserrat',sans-serif;font-weight:300;color:var(--text);background:var(--white)}

/* top bar */
.topbar{position:absolute;left:0;top:0;width:1200px;height:59px;background:var(--topbar)}
.brand{position:absolute;left:76px;top:19px;color:var(--white);font-size:21px;font-weight:400;letter-spacing:.5px;display:flex;align-items:center;gap:8px}
.brand-dot{width:9px;height:9px;border-radius:50%;background:var(--white)}
.topnav{position:absolute;top:22px;font-size:13px;color:var(--white);font-weight:400;display:flex;align-items:center;gap:5px}
.topnav.account{color:var(--teal)}
.topnav svg{width:11px;height:11px}

/* sub nav */
.subnav{position:absolute;left:0;top:59px;width:1200px;height:58px;background:var(--subnav)}
.subnav a{position:absolute;top:0;height:58px;line-height:58px;font-size:13px;font-weight:400;color:var(--ink);text-decoration:none;letter-spacing:.3px}
.subnav a.active{background:var(--pink);color:var(--white);top:8px;height:50px;line-height:42px;padding:0 16px}

/* business header */
.business-header{position:absolute;left:0;top:117px;width:1200px;height:440px;background:linear-gradient(90deg,#f3f3f3 0%,#f7f7f7 55%,#ffffff 80%,#f4f4f4 100%)}
.client-badge{position:absolute;left:80px;top:50px;width:104px;height:104px;border-radius:50%;background:#111;color:var(--white);font-size:11px;font-weight:400;display:flex;align-items:center;justify-content:center;text-align:center;line-height:1.3}
.client-name{position:absolute;left:227px;top:62px;font-size:25px;font-weight:400;color:var(--ink);letter-spacing:.8px}
.contact{position:absolute;left:227px;font-size:15px;font-weight:400;color:var(--ink);display:flex;align-items:center;gap:14px}
.contact svg{width:20px;height:16px}
.intro{position:absolute;left:76px;top:190px;width:660px;font-size:13.4px;line-height:22px;color:#444}
.intro p+p{margin-top:4px}
.hero-photo{position:absolute;left:800px;top:10px;width:285px;height:430px;border-radius:140px 140px 0 0;background:linear-gradient(180deg,#e9dcd6 0%,#e1b9c8 35%,#d7478e 70%,#c9307c 100%)}

/* who you are */
.who-card{position:absolute;left:76px;top:604px;width:1049px;height:775px;border:1px solid var(--line);background:var(--white)}
.section-title{font-size:25px;font-weight:400;color:var(--ink);text-align:center;letter-spacing:1px}
.who-card .section-title{position:absolute;top:30px;left:0;right:0}
.field{border:1px solid var(--teal);background:var(--white)}
.field-label{height:37px;background:var(--teal);color:var(--white);font-size:14px;font-weight:400;padding:0 15px;display:flex;align-items:center;justify-content:space-between}
.who-grid{position:absolute;left:16px;top:89px;display:grid;grid-template-columns:494px 494px;grid-template-rows:133px 133px 133px;column-gap:27px;row-gap:17px}
.swot-title{position:absolute;top:562px;left:0;right:0;text-align:center;font-size:16px;font-weight:500;color:var(--ink);letter-spacing:.5px}
.swot-grid{position:absolute;left:16px;top:609px;display:grid;grid-template-columns:repeat(4,240px);grid-template-rows:134px;column-gap:19.5px}

/* why you exist */
.why-section{position:absolute;left:0;top:1418px;width:1200px;height:999px;background:var(--light)}
.why-section .section-title{position:absolute;top:40px;left:0;right:0}
.why-grid{position:absolute;left:76px;top:102px;display:grid;grid-template-columns:511px 511px;grid-template-rows:repeat(5,134px);column-gap:27px;row-gap:16px}
.field.prompt{border-color:var(--pink)}
.field.prompt .field-label{background:var(--pink)}
.hint{width:13px;height:13px;border-radius:50%;background:#555;color:var(--white);font-size:9px;font-weight:600;display:flex;align-items:center;justify-content:center}
.save-btn{position:absolute;left:474px;top:879px;width:252px;height:57px;background:var(--teal);color:var(--white);font-size:16px;font-weight:500;letter-spacing:1px;display:flex;align-items:center;justify-content:center}

/* footer */
.footer{position:absolute;left:0;top:2417px;width:1200px;height:122px;background:var(--footer);text-align:center;color:var(--white)}
.copyright{position:absolute;top:27px;left:0;right:0;font-size:12.5px;font-weight:400}
.social{position:absolute;top:67px;left:0;right:0;display:flex;justify-content:center;gap:22px}
.social span{width:18px;height:18px;border-radius:50%;background:var(--white)}
</style>
</head>
<body>

<header class="topbar">
  <div class="brand">ROOTWISE <span class="brand-dot"></span></div>
  <span class="topnav" style="left:701px">Plan</span>
  <span class="topnav" style="left:758px">Learn</span>
  <span class="topnav" style="left:826px">Remember</span>
  <span class="topnav account" style="left:937px"><svg viewBox="0 0 12 12"><circle cx="6" cy="3.5" r="3" fill="currentColor"/><path d="M0 12c0-4 3-5.5 6-5.5s6 1.5 6 5.5z" fill="currentColor"/></svg>My Profile</span>
  <span class="topnav account" style="left:1054px"><svg viewBox="0 0 12 12" fill="none" stroke="currentColor" stroke-width="1.4"><path d="M5 1H1v10h4"/><path d="M4 6h7M8.5 3.5 11 6 8.5 8.5"/></svg>Log Out</span>
</header>

<nav class="subnav">
  <a class="active" style="left:76px">YOUR BUSINESS</a>
  <a style="left:235px">YOUR PRODUCTS</a>
  <a style="left:386px">YOUR CUSTOMERS</a>
  <a style="left:547px">YOUR GOALS</a>
  <a style="left:669px">YOUR PLAN</a>
</nav>

<section class="business-header">
  <div class="client-badge">Mara Linden<br>Makeup</div>
  <h1 class="client-name" style="font-weight:400;font-size:25px">MARA LINDEN MAKUP</h1>
  <div class="contact" style="top:112px">
    <svg viewBox="0 0 20 16" fill="none" stroke="#222" stroke-width="1.6"><rect x="3" y="2" width="14" height="9" rx="1"/><path d="M1 14h18"/></svg>
    maralindenmakeup.com
  </div>
  <div class="contact" style="top:156px">
    <svg viewBox="0 0 20 16"><rect x="1" y="2" width="18" height="12" rx="1" fill="#222"/><path d="M1.5 3 10 9.5 18.5 3" fill="none" stroke="#f4f4f4" stroke-width="1.4"/></svg>
    hello@maralindenmakeup.com
  </div>
  <div class="intro">
    <p>Aliquam molestie, mi et imperdiet euismod, dui purus auctor tellus, et interdum lacus lectus et ante. Sed accumsan sollicitudin sapien, sit amet adipiscing turpis gravida ac. In congue, neque ac lobortis volutpat, libero mauris varius mi, vitae suscipit ipsum ligula vitae risus. Duis aliquam nibh a dui iaculis viverra id a velit.</p>
    <p>Vivamus egestas risus in magna varius commodo. Sed semper viverra egestas. Etiam pretium porttitor lectus, vel ornare neque porta volutpat.<br>Aenean a nibh eget turpis vehicula tempus ac sed massa. Vestibulum dolor nulla, ultrices ac tincidunt sed, laoreet non est. Suspendisse lobortis turpis in odio blandit ac interdum lorem euismod. Etiam risus massa, vulputate eu pellentesque et, consectetur a neque.</p>
  </div>
  <div class="hero-photo" role="img" aria-label="Photo of a smiling makeup artist in a pink tunic holding makeup brushes"></div>
</section>

<section class="who-card">
  <h2 class="section-title">WHO YOU ARE</h2>
  <div class="who-grid">
    <div class="field"><div class="field-label">Business name</div></div>
    <div class="field"><div class="field-label">Business tag line</div></div>
    <div class="field"><div class="field-label">Business vision</div></div>
    <div class="field"><div class="field-label">Business bio</div></div>
    <div class="field"><div class="field-label">Brand colours</div></div>
    <div class="field"><div class="field-label">Key competitors</div></div>
  </div>
  <h3 class="swot-title">SWOT ANALYSIS</h3>
  <div class="swot-grid">
    <div class="field"><div class="field-label">Strengths</div></div>
    <div class="field"><div class="field-label">Weaknesses</div></div>
    <div class="field"><div class="field-label">Opportunities</div></div>
    <div class="field"><div class="field-label">Threats</div></div>
  </div>
</section>

<section class="why-section">
  <h2 class="section-title">WHY YOU EXIST</h2>
  <div class="why-grid">
    <div class="field prompt"><div class="field-label">Who are your ideal customers?<span class="hint">i</span></div></div>
    <div class="field prompt"><div class="field-label">What problem are you trying to solve for them?<span class="hint">?</span></div></div>
    <div class="field prompt"><div class="field-label">What pain points will this remove for them?<span class="hint">i</span></div></div>
    <div class="field prompt"><div class="field-label">How do you solve it?<span class="hint">i</span></div></div>
    <div class="field prompt"><div class="field-label">How else could this problem be solved?<span class="hint">i</span></div></div>
    <div class="field prompt"><div class="field-label">Who offers these other solutions?<span class="hint">i</span></div></div>
    <div class="field prompt"><div class="field-label">Why is your solution better?<span class="hint">i</span></div></div>
    <div class="field prompt"><div class="field-label">How much does your solution cost?<span class="hint">i</span></div></div>
    <div class="field prompt"><div class="field-label">What value are you providing to justify this cost?<span class="hint">i</span></div></div>
    <div class="field prompt"><div class="field-label">How will this make their life/job easier/better?<span class="hint">i</span></div></div>
  </div>
  <div class="save-btn">SAVE CHANGES</div>
</section>

<footer class="footer">
  <p class="copyright">Copyright © 2017.Company Name. All Right Reserved</p>
  <div class="social"><span></span><span></span><span></span><span></span><span></span></div>
</footer>

</body>
</html>
```